Business Card Design for company

We want new business cards. We'd like something different-- yet still highly professional. Our tagline is Providing leadership, delivering success. Stock photos are ok, as long as they are relevant and look upscale.

Target Market(s)

Architecture/Business Management Consulting/Engineering Consulting

Contact Information for Business Card

dark gray background with pops of blue might be good, but you tell me. You're the designers. Rounded corners might be nice, but again, you tell me.

Font styles to use
Serif
Sans Serif

Colors
3276b5
5c5c5c
9d9d9d
fbfbfb

Requirements
Nice to have
• Something different, but still very professional.

```html
<!DOCTYPE html>
<html lang="en">
<head>
<meta charset="utf-8">
<title>Halvern Partners – Business Cards</title>
<link rel="stylesheet" href="https://fonts.googleapis.com/css2?family=Open+Sans:wght@400;600;700&display=swap">
<style>
  :root {
    --brand-blue: #2b6398;
    --accent-blue: #3276b5;
    --text-gray: #5c5c5c;
    --line-gray: #9d9d9d;
    --card-white: #fbfbfb;
    --backdrop: #2a2b2d;
  }
  * { margin: 0; padding: 0; box-sizing: border-box; }
  html, body { width: 1200px; height: 885px; overflow: hidden; }
  body {
    background: var(--backdrop);
    font-family: "Open Sans", Arial, sans-serif;
    position: relative;
  }
  .card {
    position: absolute;
    background: var(--card-white);
    box-shadow: 0 10px 30px rgba(0,0,0,0.45);
  }

  /* Front card */
  .card-front {
    left: 80px; top: 70px;
    width: 560px; height: 320px;
  }
  .front-brand {
    position: absolute;
    left: 0; right: 0; top: 105px;
    display: flex; align-items: center; justify-content: center; gap: 14px;
  }
  .brand-mark {
    width: 26px; height: 26px;
    background: var(--accent-blue);
  }
  .brand-name {
    font-weight: 600;
    font-size: 34px;
    letter-spacing: 1px;
    color: var(--accent-blue);
    white-space: nowrap;
  }
  .tagline {
    position: absolute;
    left: 0; right: 0; top: 210px;
    text-align: center;
    font-size: 15px;
    color: var(--text-gray);
  }
  .tagline .dot {
    display: inline-block;
    width: 6px; height: 6px;
    border-radius: 50%;
    background: var(--accent-blue);
    vertical-align: middle;
    margin: 0 8px;
  }

  /* Back card */
  .card-back {
    left: 470px; top: 430px;
    width: 620px; height: 355px;
  }
  .back-band {
    position: absolute;
    left: 0; right: 0; top: 52px;
    height: 140px;
    background: var(--brand-blue);
    display: flex; align-items: center; justify-content: center; gap: 14px;
  }
  .back-band .brand-name { color: #ffffff; font-size: 38px; }
  .back-band .brand-mark { background: #ffffff; }

  .back-details {
    position: absolute;
    left: 0; right: 0; top: 225px;
    display: flex; justify-content: center;
  }
  .person {
    width: 260px;
    text-align: right;
    padding-right: 22px;
    color: var(--text-gray);
    font-size: 15px;
    line-height: 1.35;
  }
  .person-name {
    font-weight: 700;
    font-size: 21px;
    color: var(--brand-blue);
    line-height: 1.1;
  }
  .person-title { font-size: 15px; text-transform: uppercase; margin-bottom: 4px; }
  .divider {
    width: 1px; height: 90px;
    background: linear-gradient(var(--line-gray), rgba(157,157,157,0.2));
  }
  .contacts {
    list-style: none;
    padding-left: 22px;
    width: 300px;
    color: var(--text-gray);
    font-size: 14px;
  }
  .contacts li {
    display: flex; align-items: center; gap: 10px;
    height: 21px;
    white-space: nowrap;
  }
  .contacts svg { width: 14px; height: 14px; flex: none; fill: var(--brand-blue); }
</style>
</head>
<body>

  <section class="card card-front" aria-label="Business card front">
    <div class="front-brand">
      <span class="brand-mark"></span>
      <span class="brand-name">HALVERN PARTNERS</span>
    </div>
    <p class="tagline">Guiding strategy<span class="dot"></span>building results</p>
  </section>

  <section class="card card-back" aria-label="Business card back">
    <div class="back-band">
      <span class="brand-mark"></span>
      <span class="brand-name">HALVERN PARTNERS</span>
    </div>

    <div class="back-details">
      <div class="person">
        <p class="person-name">DANIEL MARSH</p>
        <p class="person-title">President</p>
        <p class="address">2140 Alder Crest Lane<br>Ashford Hills, NY 10000</p>
      </div>
      <div class="divider"></div>
      <ul class="contacts">
        <li>
          <svg viewBox="0 0 16 16" aria-hidden="true"><path d="M2 5c0-2 2-3 6-3s6 1 6 3v1h-3V4.5H5V6H2z"/><rect x="3" y="7" width="10" height="7" rx="1"/></svg>
          555 0142 7781
        </li>
        <li>
          <svg viewBox="0 0 16 16" aria-hidden="true"><path d="M4 1h8v14H4zM5.5 2.5v9h5v-9z" fill-rule="evenodd"/></svg>
          555 0187 3094
        </li>
        <li>
          <svg viewBox="0 0 16 16" aria-hidden="true"><path d="M1 3h14v10H1zM2.5 4.5 8 9l5.5-4.5z" fill-rule="evenodd"/></svg>
          daniel@halvernpartners.com
        </li>
        <li>
          <svg viewBox="0 0 16 16" aria-hidden="true"><circle cx="8" cy="8" r="7"/><path d="M4 8h8M8 2v12" stroke="#fbfbfb" stroke-width="1.2"/></svg>
          www.halvernpartners.com
        </li>
      </ul>
    </div>
  </section>

</body>
</html>
```